Electronics Recycling and IT Asset Disposition Flyer and Brochure Design

We need a 2 side A5 Flyer and 4 side A4 folder( brochure) for our electronics waste recycling and IT asset management and disposition business.
Our business provides free electronics waste recycling for companies, schools, learning institutions,councils, IT companies and government sectors. Many people are ignorant of responsible recycling of electronics which could harm our health if not treated properly.
The list of other services attached in the pdf.
We provide an end to end and tailored solution for our customers from collection, logistics, data sanitisation, remarketing and recycling.

The Flyer should create awareness of responsible electronics recycling and drive the audience to contact us or go to our website to learn more about the company and services.A brief list of services should also be included in the flyer.The goal is to get the audience to contact us to enquire more about our services.

The Brochure should include all the above plus provide more details about the company, processes, services,contact details (fb, linkedin,Twitter). The goal is to convert the audience to customers for recycling and provide other services as added services.

The final design for both flyer and brochure should communicate responsible recycling of electronic scrap and tailored solution for every organisation.

The company website is www.kelvane-scrap.com.au based in Australia. We serve clients nationwide.

Target Market(s)

IT companies, Corporate, schools and learning institutions, government sector

Industry/Entity Type

Recycling

Contact Information for Business Card

Name: Harold Pendrake
email: harold@kelvane-scrap.com.au
website: www.kelvane-scrap.com.au
mobile: +614 612 39057
Phone: 1300 46 2735

Font styles to use
Serif

Requirements
Must have
• I would like the designs to have more images and icons
Nice to have
Should not have
• none

```html
<!DOCTYPE html>
<html lang="en">
<head>
<meta charset="utf-8">
<title>Kelvane Scrap – Service Offering and E-waste Recycling Flyer</title>
<link rel="stylesheet" href="https://fonts.googleapis.com/css2?family=Open+Sans:wght@400;600;700&display=swap">
<style>
  :root{
    --green:#5fae3b;
    --green-dark:#2f7d32;
    --green-deep:#1f5a24;
    --green-light:#8cc63f;
    --grey-band:#ececec;
    --grey-text:#6b6b6b;
    --grey-dark:#555a5c;
    --ink:#3a3a3a;
    --paper:#ffffff;
    --stage:#e4e4e2;
  }
  *{box-sizing:border-box;margin:0;padding:0}
  html,body{width:1200px;height:675px;overflow:hidden}
  body{background:var(--stage);font-family:"Open Sans",Arial,sans-serif;color:var(--ink);position:relative}

  .page{position:absolute;top:26px;width:440px;height:622px;background:var(--paper);overflow:hidden;box-shadow:0 2px 10px rgba(0,0,0,.18)}
  .page--services{left:140px}
  .page--recycling{left:620px}

  /* ---------- Services side ---------- */
  .hero{position:absolute;top:58px;left:0;width:100%;height:140px;
        background:linear-gradient(135deg,#3f5a3a 0%,#6f8b55 35%,#4c6b45 60%,#8fb36a 100%)}
  .hero__overlay{position:absolute;left:0;bottom:0;width:100%;height:70px;
        background:linear-gradient(180deg,rgba(95,174,59,0) 0%,rgba(95,174,59,.85) 100%)}
  .brand-badge{position:absolute;top:16px;left:50%;transform:translateX(-50%);
        width:70px;height:70px;border-radius:50%;background:var(--paper);border:3px solid var(--green);
        display:flex;align-items:center;justify-content:center;text-align:center;z-index:2}
  .brand-badge span{font-size:9px;font-weight:700;color:var(--green);line-height:1.1}
  .hero-icons{position:absolute;top:110px;left:0;width:100%;display:flex;justify-content:center;gap:10px;z-index:2}
  .hero-icons svg{width:26px;height:26px}
  .hero__title{position:absolute;top:146px;width:100%;text-align:center;color:#fff;font-size:24px;font-weight:600;z-index:2;letter-spacing:.3px}
  .service-bar{position:absolute;top:198px;left:0;width:100%;height:22px;background:var(--green);
        color:#fff;font-size:11px;font-weight:700;text-align:center;line-height:22px}

  .services{position:absolute;top:222px;left:0;width:100%}
  .service{display:flex;align-items:flex-start;padding:4px 18px 4px 30px}
  .service:nth-child(even){background:var(--grey-band)}
  .service__icon{flex:0 0 26px;height:26px;margin-right:18px;margin-top:3px}
  .service__icon svg{width:26px;height:26px}
  .service__head{font-size:9.6px;font-weight:700;color:var(--green);line-height:1.3;margin-bottom:1px;white-space:nowrap}
  .service__text{font-size:6.2px;color:var(--grey-text);line-height:1.45}
  .service--intro{padding-left:74px}

  .foot-bands{position:absolute;bottom:0;left:0;width:100%;height:26px;display:flex}
  .foot-bands i{display:block;height:100%}

  /* ---------- Recycling side ---------- */
  .top-rule{position:absolute;top:38px;left:0;width:100%;height:2px;background:var(--green)}
  .top-rule::after{content:"";position:absolute;left:180px;top:-2px;width:80px;height:4px;background:var(--green)}
  .cycle{position:absolute;top:48px;left:100px;width:180px;height:180px}
  .brand-line{position:absolute;top:160px;left:330px;display:flex;align-items:center;gap:6px}
  .brand-line i{display:block;width:22px;height:22px;border-radius:50%;border:2px solid var(--green)}
  .brand-line span{font-size:9.5px;font-weight:600;color:var(--green);line-height:1.2}

  .logistics{position:absolute;top:232px;left:0;width:100%;height:84px;background:var(--grey-band);text-align:center;padding-top:5px}
  .section-icon{width:22px;height:22px;display:block;margin:0 auto}
  .section-title{font-size:10.5px;font-weight:700;color:var(--green);margin-top:1px}
  .section-text{font-size:6.2px;color:var(--grey-text);line-height:1.5;padding:2px 36px 0;text-align:center}

  .industries{position:absolute;top:324px;left:0;width:100%;text-align:center}
  .industries .section-text{padding-top:4px}
  .industries__intro{text-align:left;padding:18px 52px 0;font-size:6.5px;color:var(--grey-text);line-height:1.5}
  .industry-list{list-style:none;text-align:left;padding:4px 0 0 64px;font-size:6.5px;color:var(--grey-text);line-height:1.55}
  .industry-list li::before{content:"";display:inline-block;width:4px;height:4px;background:var(--green);margin-right:6px;vertical-align:middle}

  .contact{position:absolute;top:440px;right:40px;text-align:right;font-size:6.8px;color:var(--grey-text);line-height:3}
  .address-band{position:absolute;bottom:0;left:0;width:100%;height:30px;display:flex}
  .address-band i{display:block;height:100%}
  .address{position:absolute;bottom:0;right:0;width:62%;height:30px;line-height:30px;padding-left:14px;color:#fff;font-size:8px}
</style>
</head>
<body>

<!-- Services side -->
<section class="page page--services">
  <div class="hero" role="img" aria-label="Close-up photograph of a green circuit board with electronic components">
    <div class="hero__overlay"></div>
  </div>
  <div class="brand-badge"><span>Kelvane<br>Scrap</span></div>

  <div class="hero-icons" aria-hidden="true">
    <svg viewBox="0 0 26 26"><circle cx="13" cy="13" r="12" fill="#fff"/><circle cx="13" cy="13" r="9" fill="var(--green)"/><path d="M9 13a4 4 0 0 1 7-2.6M17 13a4 4 0 0 1-7 2.6" stroke="#fff" stroke-width="1.4" fill="none"/></svg>
    <svg viewBox="0 0 26 26"><circle cx="13" cy="13" r="12" fill="#fff"/><circle cx="13" cy="13" r="9" fill="var(--green)"/><rect x="9.5" y="8" width="7" height="10" fill="#fff"/></svg>
    <svg viewBox="0 0 26 26"><circle cx="13" cy="13" r="12" fill="#fff"/><circle cx="13" cy="13" r="9" fill="var(--green)"/><ellipse cx="13" cy="10" rx="4" ry="1.6" fill="#fff"/><rect x="9" y="10" width="8" height="6" fill="#fff"/></svg>
    <svg viewBox="0 0 26 26"><circle cx="13" cy="13" r="12" fill="#fff"/><circle cx="13" cy="13" r="9" fill="var(--green)"/><circle cx="13" cy="13" r="3.5" stroke="#fff" stroke-width="1.5" fill="none"/></svg>
    <svg viewBox="0 0 26 26"><circle cx="13" cy="13" r="12" fill="#fff"/><circle cx="13" cy="13" r="9" fill="var(--green)"/><path d="M9 9l8 8M17 9l-8 8" stroke="#fff" stroke-width="1.6"/></svg>
    <svg viewBox="0 0 26 26"><circle cx="13" cy="13" r="12" fill="#fff"/><circle cx="13" cy="13" r="9" fill="var(--green)"/><circle cx="13" cy="13" r="4" stroke="#fff" stroke-width="2" stroke-dasharray="2 1.2" fill="none"/></svg>
  </div>
  <h1 class="hero__title">Service Offering</h1>
  <div class="service-bar">Secure E-Waste Collection Service</div>

  <div class="services">
    <div class="service service--intro">
      <p class="service__text">Kelvane Scrap collects electronic waste from schools, businesses, home users and government departments<br>
      Secure collection includes pick up of e-waste and transportation to our recycling facility in a<br>
      Secured truck<br>Registration of assets and reporting</p>
    </div>
    <div class="service">
      <div class="service__icon"><svg viewBox="0 0 26 26"><circle cx="13" cy="13" r="12" fill="none" stroke="var(--green)"/><circle cx="13" cy="13" r="9" fill="var(--green)"/><path d="M9 13a4 4 0 0 1 7-2.6M17 13a4 4 0 0 1-7 2.6" stroke="#fff" stroke-width="1.4" fill="none"/></svg></div>
      <div><h2 class="service__head">Receipting Registration, Test and Audit Services</h2>
      <p class="service__text">Registering your assets on our Asset Management System<br>Test, audit and verify functionality, condition and resale value. Provide a detailed asset report<br>Clearing and removal of company logos and asset tags</p></div>
    </div>
    <div class="service">
      <div class="service__icon"><svg viewBox="0 0 26 26"><circle cx="13" cy="13" r="12" fill="none" stroke="var(--green)"/><circle cx="13" cy="13" r="9" fill="var(--green)"/><rect x="9.5" y="8" width="7" height="10" fill="#fff"/></svg></div>
      <div><h2 class="service__head">Certified Data Erasure Services</h2>
      <p class="service__text">To provide secure data destruction:<br>3 pass (Commercial &amp; DoD standard)<br>7 pass<br>Total destruction of HDDs by degausser<br>Total physical destruction of any storage media by shredding</p></div>
    </div>
    <div class="service">
      <div class="service__icon"><svg viewBox="0 0 26 26"><circle cx="13" cy="13" r="12" fill="none" stroke="var(--green)"/><circle cx="13" cy="13" r="9" fill="var(--green)"/><ellipse cx="13" cy="10" rx="4" ry="1.6" fill="#fff"/><rect x="9" y="10" width="8" height="6" fill="#fff"/></svg></div>
      <div><h2 class="service__head">IT Asset Remarketing</h2>
      <p class="service__text">Recover client's IT asset and mobile devices for valuation and remarketing</p></div>
    </div>
    <div class="service">
      <div class="service__icon"><svg viewBox="0 0 26 26"><circle cx="13" cy="13" r="12" fill="none" stroke="var(--green)"/><circle cx="13" cy="13" r="9" fill="var(--green)"/><circle cx="13" cy="13" r="3.5" stroke="#fff" stroke-width="1.5" fill="none"/></svg></div>
      <div><h2 class="service__head">Processing &amp; recycling of electronic waste</h2>
      <p class="service__text">All assets with no market value will be processed as E-Waste and recycled with zero to landfill<br>in our ISO certified partner refinery overseas for metals recovery</p></div>
    </div>
    <div class="service">
      <div class="service__icon"><svg viewBox="0 0 26 26"><circle cx="13" cy="13" r="12" fill="none" stroke="var(--green)"/><circle cx="13" cy="13" r="9" fill="var(--green)"/><path d="M9 9l8 8M17 9l-8 8" stroke="#fff" stroke-width="1.6"/></svg></div>
      <div><h2 class="service__head">IT Services &amp; Data Center Setup, Relocation and Decommissioning</h2>
      <p class="service__text">Deployment, relocation and decommissioning of IT systems by professional Norvane and Tessel<br>certified engineers<br>Data Center decommissioning/racking/de-racking and relocation<br>IT Systems deployment and support for small and medium size business</p></div>
    </div>
    <div class="service">
      <div class="service__icon"><svg viewBox="0 0 26 26"><circle cx="13" cy="13" r="12" fill="none" stroke="var(--green)"/><circle cx="13" cy="13" r="9" fill="var(--green)"/><circle cx="13" cy="13" r="4" stroke="#fff" stroke-width="2" stroke-dasharray="2 1.2" fill="none"/></svg></div>
      <div><h2 class="service__head">IT Asset Auditing</h2>
      <p class="service__text">Recording of Manufacturer and Model per asset (additionally HDD quantity and capacity for<br>Server &amp; Storage assets)</p></div>
    </div>
  </div>

  <div class="foot-bands">
    <i style="width:50%;background:var(--grey-band)"></i>
    <i style="width:12%;background:var(--green-deep)"></i>
    <i style="width:38%;background:var(--green)"></i>
  </div>
</section>

<!-- Recycling side -->
<section class="page page--recycling">
  <div class="top-rule"></div>

  <svg class="cycle" viewBox="0 0 180 180" role="img" aria-label="Three-step cycle: reuse, recover, recycle">
    <circle cx="90" cy="90" r="66" fill="none" stroke="var(--green)" stroke-width="40" stroke-dasharray="134 281" transform="rotate(-200 90 90)"/>
    <circle cx="90" cy="90" r="66" fill="none" stroke="#f3f3f3" stroke-width="40" stroke-dasharray="134 281" transform="rotate(-65 90 90)"/>
    <circle cx="90" cy="90" r="66" fill="none" stroke="var(--grey-dark)" stroke-width="40" stroke-dasharray="134 281" transform="rotate(70 90 90)"/>
    <circle cx="90" cy="90" r="86" fill="none" stroke="#d6d6d6" stroke-width="1"/>
    <circle cx="90" cy="90" r="34" fill="#fff" stroke="#e2e2e2" stroke-width="3"/>
    <text x="90" y="86" text-anchor="middle" font-size="10" font-weight="700" fill="#333">E-waste</text>
    <text x="90" y="99" text-anchor="middle" font-size="10" font-weight="700" fill="#333">Recycling</text>
    <text x="70" y="40" font-size="22" font-weight="700" fill="#fff">01</text>
    <text x="34" y="60" font-size="6" font-weight="700" fill="#fff">REUSE</text>
    <text x="126" y="60" font-size="6" font-weight="700" fill="#555">RECOVER</text>
    <path d="M130 36l8 8M138 36l-8 8" stroke="#555" stroke-width="2"/>
    <text x="132" y="104" font-size="22" font-weight="700" fill="#333">02</text>
    <text x="40" y="150" font-size="22" font-weight="700" fill="#fff">03</text>
    <text x="78" y="144" font-size="6" font-weight="700" fill="#fff">RECYCLE</text>
  </svg>

  <div class="brand-line"><i></i><span>Kelvane<br>Scrap</span></div>

  <div class="logistics">
    <svg class="section-icon" viewBox="0 0 22 22"><circle cx="11" cy="11" r="10" fill="var(--green)"/><rect x="5" y="8" width="8" height="6" fill="#fff"/><rect x="13" y="10" width="4" height="4" fill="#fff"/></svg>
    <h2 class="section-title">Logistics</h2>
    <p class="section-text">We manage the collection and sorting of equipment carefully so that they are not damaged during the process of loading or transportation. This is to ensure any refurbishable or working items keep their value. Secured trucks move all the way to our handling facility, where each device is manually checked and sorted according to its type and condition by our dedicated collection team.</p>
  </div>

  <div class="industries">
    <svg class="section-icon" viewBox="0 0 22 22"><circle cx="11" cy="11" r="10" fill="var(--green)"/><path d="M6 15h10M8 15V9h6v6" stroke="#fff" stroke-width="1.6" fill="none"/></svg>
    <h2 class="section-title">Industries Served</h2>
    <p class="section-text">No matter how big or small your organisation is or how complex or simple your IT systems are, we listen to the needs of your organisation to deliver a tailored, safe and responsible solution for every device. Our dedicated team is ready to serve you.</p>
    <p class="industries__intro">Industries we serve:</p>
    <ul class="industry-list">
      <li>Corporate</li>
      <li>IT&amp;D Companies</li>
      <li>Financial Institutions</li>
      <li>Education &amp; Learning Institutions</li>
      <li>Councils</li>
      <li>Recycling companies</li>
      <li>Government sector</li>
    </ul>
  </div>

  <div class="contact">
    <p>1300 46 2735</p>
    <p>www.kelvane-scrap.com.au</p>
  </div>

  <div class="address-band">
    <i style="width:38%;background:var(--grey-band)"></i>
    <i style="width:12%;background:var(--green-deep)"></i>
    <i style="width:50%;background:var(--green)"></i>
  </div>
  <p class="address">14-20 Marrow Street, Westbury 2163 NSW</p>
</section>

</body>
</html>
```